I require a logo design and business card design.

The logo and business card is for a pre existing salon that I have purchased in the last 6 months. It is about to get a total facelift and so requires rebranding. It is currently very dated and only appeals to an older demographic, I'm hoping to keep existing clients but also encourage new and younger clients who will have more creative work done. The salon is in a seaside location, we have tourists as clients also. I would like the logo to reflect the creative nature of my business.
Target Market(s)
All ages, men and women. Middle to upper price demographic.
Industry/Entity Type
Business
Contact Information for Business Card
Logo on the front. Logo, address and phone number on the back.
Font styles to use
Colors
Designer to choose colors to be used in the design.
Requirements
Must have
- On the back of the card I also require 'next appointment details (date and time). As well as the salon name 'bluetide hair studio', the phone number 0251938462, and address 17 Wattlebrook road Saltmere.

Nice to have
- The salon has round mirrors, that could be part of a theme. It is also located in a coastal region, so that could be part of a theme.

Should not have
- Not too busy please

```html
<!DOCTYPE html>
<html lang="en">
<head>
<meta charset="utf-8">
<title>Bluetide Hair Studio – Business Card</title>
<link rel="stylesheet" href="https://fonts.googleapis.com/css2?family=Open+Sans:wght@300;400;600;700&display=swap">
<style>
  :root {
    --backdrop: #6b6b6b;
    --card-dark: #000000;
    --card-light: #f4f4f4;
    --ink-dark: #1a1a1a;
    --ink-mid: #333333;
    --ink-light: #ffffff;
    --rule: #2a2a2a;
  }
  * { box-sizing: border-box; margin: 0; padding: 0; }
  html, body {
    width: 1200px;
    height: 904px;
    overflow: hidden;
  }
  body {
    background: var(--backdrop);
    font-family: "Open Sans", Arial, sans-serif;
    display: flex;
    flex-direction: column;
    align-items: center;
    justify-content: center;
    gap: 56px;
  }
  .card {
    width: 640px;
    height: 366px;
    position: relative;
    box-shadow: 0 6px 18px rgba(0,0,0,0.35);
  }
  .card--front {
    background: var(--card-dark);
    display: flex;
    align-items: center;
    justify-content: center;
  }
  .card--back {
    background: var(--card-light);
    color: var(--ink-mid);
    display: flex;
    flex-direction: column;
    align-items: center;
    padding-top: 40px;
  }
  .brand {
    display: flex;
    align-items: center;
    gap: 14px;
    font-weight: 300;
    letter-spacing: 0.12em;
    text-transform: uppercase;
    white-space: nowrap;
  }
  .brand__dot {
    border-radius: 50%;
    border: 2px solid currentColor;
    flex: 0 0 auto;
  }
  .card--front .brand {
    color: var(--ink-light);
    font-size: 26px;
  }
  .card--front .brand__dot { width: 34px; height: 34px; }
  .card--back .brand {
    color: var(--ink-dark);
    font-size: 28px;
  }
  .card--back .brand__dot { width: 36px; height: 36px; }
  .appointment {
    margin-top: 36px;
    width: 520px;
    font-size: 17px;
    font-weight: 400;
    color: var(--ink-mid);
  }
  .appointment__intro { text-align: center; }
  .appointment__line {
    display: flex;
    align-items: flex-end;
    gap: 8px;
    margin-top: 18px;
  }
  .appointment__blank {
    flex: 1;
    border-bottom: 2px dotted var(--rule);
    height: 18px;
  }
  .appointment__blank--short { flex: 0 0 130px; }
  .contact {
    margin-top: 36px;
    text-align: center;
  }
  .contact__phone {
    font-size: 20px;
    font-weight: 700;
    color: var(--ink-dark);
  }
  .contact__address {
    font-size: 17px;
    font-weight: 400;
    color: var(--ink-mid);
    margin-top: 2px;
  }
</style>
</head>
<body>
  <section class="card card--front" aria-label="Card front">
    <div class="brand">
      <span class="brand__dot"></span>
      <span class="brand__name">bluetide hair studio</span>
    </div>
  </section>

  <section class="card card--back" aria-label="Card back">
    <div class="brand">
      <span class="brand__dot"></span>
      <span class="brand__name">bluetide hair studio</span>
    </div>

    <div class="appointment">
      <p class="appointment__intro">Your next appointment is</p>
      <div class="appointment__line">
        <span class="appointment__blank"></span>
        <span>at</span>
        <span class="appointment__blank appointment__blank--short"></span>
        <span>am/pm</span>
      </div>
    </div>

    <div class="contact">
      <p class="contact__phone">(02) 5193 8462</p>
      <p class="contact__address">17 Wattlebrook road Saltmere</p>
    </div>
  </section>
</body>
</html>
```